Business Card Design for company

We want new business cards. We'd like something different-- yet still highly professional. Our tagline is Providing leadership, delivering success. Stock photos are ok, as long as they are relevant and look upscale.

Target Market(s)

Architecture/Business Management Consulting/Engineering Consulting

Contact Information for Business Card

dark gray background with pops of blue might be good, but you tell me. You're the designers. Rounded corners might be nice, but again, you tell me.

Font styles to use
Serif
Sans Serif

Colors
3276b5
5c5c5c
9d9d9d
fbfbfb

Requirements
Nice to have
• Something different, but still very professional.

```html
<!DOCTYPE html>
<html lang="en">
<head>
<meta charset="utf-8">
<title>Arvell Group — Business Card</title>
<link href="https://fonts.googleapis.com/css2?family=Montserrat:wght@600&family=Open+Sans:wght@400;600&display=swap" rel="stylesheet">
<style>
  :root{
    --backdrop:#2a2b2d;
    --paper:#f3f3f3;
    --brand-blue:#255b8c;
    --slate:#45484c;
    --ink-light:#ffffff;
    --ink-soft:#dfe6ee;
  }
  *{box-sizing:border-box;margin:0;padding:0}
  html,body{width:1200px;height:923px;overflow:hidden}
  body{background:var(--backdrop);display:flex;align-items:center;justify-content:center;font-family:"Open Sans",sans-serif}
  .card{position:relative;width:1000px;height:571px;background:var(--paper);overflow:hidden;box-shadow:0 20px 50px rgba(0,0,0,.45)}
  .card-shapes{position:absolute;inset:0;width:100%;height:100%}
  .brand{position:absolute;left:70px;top:170px;display:flex;align-items:flex-start;gap:18px}
  .brand-mark{flex:none;width:22px;height:22px;background:var(--brand-blue);margin-top:14px}
  .brand-name{font-family:"Montserrat",sans-serif;font-weight:600;font-size:52px;line-height:1.08;letter-spacing:3px;color:var(--slate);text-transform:uppercase}
  .brand-name span{display:block}
  .nameplate{position:absolute;left:660px;top:60px;width:310px;height:110px;background:var(--slate);display:flex;flex-direction:column;justify-content:center;align-items:flex-end;padding-right:48px;color:var(--ink-light)}
  .nameplate-name{font-size:30px;font-weight:600;line-height:1.15}
  .nameplate-role{font-size:16px;color:var(--ink-soft)}
  .contact{position:absolute;right:40px;top:240px;display:flex;flex-direction:column;gap:7px;color:var(--ink-light);font-size:17px;text-align:right}
  .contact-row{display:flex;align-items:flex-start;justify-content:flex-end;gap:14px}
  .contact-icon{flex:none;width:20px;height:20px;background:var(--ink-light);border-radius:3px;margin-top:2px}
  .contact-icon svg{width:20px;height:20px;display:block}
  .contact-address{line-height:1.25}
</style>
</head>
<body>
  <div class="card">
    <svg class="card-shapes" viewBox="0 0 1000 571" preserveAspectRatio="none" aria-hidden="true">
      <polygon points="470,0 530,0 600,571 530,571" fill="var(--slate)"/>
      <polygon points="530,0 1000,0 1000,571 600,571" fill="var(--brand-blue)"/>
    </svg>

    <div class="brand">
      <span class="brand-mark"></span>
      <span class="brand-name"><span>Arvell</span><span>Group</span></span>
    </div>

    <div class="nameplate">
      <span class="nameplate-name">Daniel Hartley</span>
      <span class="nameplate-role">Owner</span>
    </div>

    <div class="contact">
      <div class="contact-row">
        <span>+0000-0000-0000</span>
        <span class="contact-icon"><svg viewBox="0 0 20 20"><path d="M6 4l3 3-2 2c1 2 2 3 4 4l2-2 3 3-2 2C9 16 4 11 4 6z" fill="var(--brand-blue)"/></svg></span>
      </div>
      <div class="contact-row">
        <span>info@yourdomain.com</span>
        <span class="contact-icon"><svg viewBox="0 0 20 20"><rect x="4" y="6" width="12" height="8" fill="none" stroke="var(--brand-blue)" stroke-width="1.6"/><path d="M4 6l6 5 6-5" fill="none" stroke="var(--brand-blue)" stroke-width="1.6"/></svg></span>
      </div>
      <div class="contact-row">
        <span>www.yourdomain.com</span>
        <span class="contact-icon"><svg viewBox="0 0 20 20"><circle cx="10" cy="10" r="6" fill="none" stroke="var(--brand-blue)" stroke-width="1.6"/><path d="M4 10h12M10 4c-3 3-3 9 0 12M10 4c3 3 3 9 0 12" fill="none" stroke="var(--brand-blue)" stroke-width="1.2"/></svg></span>
      </div>
      <div class="contact-row">
        <span class="contact-address">Suite 210,<br>48 Marlow Street,<br>London</span>
        <span class="contact-icon"><svg viewBox="0 0 20 20"><path d="M10 17s-5-5-5-8.5a5 5 0 0110 0C15 12 10 17 10 17z" fill="var(--brand-blue)"/><circle cx="10" cy="8.5" r="1.8" fill="var(--ink-light)"/></svg></span>
      </div>
    </div>
  </div>
</body>
</html>
```